Harborview Estates Business Card for Apartment Buildings

Create business cards for resident managers who run apartment buildings. The audience is the public who are searching for apartment rentals, and current residents who live at the apartment building. Key design element will be incorporating the company logo, however, the logo cannot dominate. The building name and manager name are more important than the logo. Current business card design leaves little room for copy, so we may need to reduce the size on the current card to allow for more space for copy.

Target Market(s)

Adults 18-65 years of age, who are looking for an apartment rental, plus current residents who live at our apartment buildings.

Industry/Entity Type

Property Management

Contact Information for Business Card

A major design element will be use of the company logo. Important property and manager contact information must be part of the design. The size of the logo will need to be reduced to make room for building and manager contact copy.

Font styles to use
Sans Serif

Colors
3176b5
000000
959595
ffffff

Requirements
Must have
• 1) Incorporate the company logo.
• 2) Use the company colors (dark blue, black/grey, over white).
• 3) FEATURE THE BUILDING NAME
• 4) FEATURE THE MANAGER NAME
• 5) The company name is less important than BUILDING and MANAGER
• 6) Manager contact information
• **SEE ATTACHED CREATIVE BRIEF**
Nice to have
• 1) Back of card logo watermark
• 2) Ability to write notes on back of carfd
Should not have
• Avoid letting the company logo dominate the card, the building name and manager are more important than the company logo.

```html
<!DOCTYPE html>
<html lang="en">
<head>
<meta charset="utf-8">
<title>Harborview Estates – Resident Manager Business Card</title>
<link rel="stylesheet" href="https://fonts.googleapis.com/css2?family=Lato:wght@400;700;900&display=swap">
<style>
  :root {
    --brand-blue: #3176b5;
    --ink: #000000;
    --band: #1d1d1d;
    --mid-grey: #959595;
    --paper: #ffffff;
    --watermark: #ececec;
    --stage: #8d9293;
  }
  * { box-sizing: border-box; margin: 0; padding: 0; }
  html, body { width: 1200px; height: 1000px; overflow: hidden; }
  body {
    background: radial-gradient(ellipse at 45% 35%, #a3a8a8 0%, var(--stage) 55%, #6f7475 100%);
    font-family: "Lato", Arial, sans-serif;
    position: relative;
  }
  .card {
    position: absolute;
    background: var(--paper);
    overflow: hidden;
    box-shadow: 0 6px 18px rgba(0,0,0,0.28);
  }

  /* Front */
  .card-front { left: 80px; top: 330px; width: 560px; height: 320px; }
  .front-band {
    position: absolute; left: 0; top: 0; width: 100%; height: 110px;
    background: var(--band);
  }
  .manager { position: absolute; right: 26px; top: 38px; text-align: right; color: var(--paper); }
  .manager-name { font-size: 25px; letter-spacing: 0.3px; line-height: 1.1; }
  .manager-name .first { font-weight: 900; }
  .manager-name .last { font-weight: 400; }
  .manager-title { font-size: 15px; font-weight: 400; margin-top: 2px; }

  .brand-tab {
    position: absolute; left: 0; top: 110px; width: 150px; height: 100px;
    background: var(--brand-blue);
    border-radius: 0 50px 50px 0;
  }
  .brand-seal {
    position: absolute; left: 52px; top: 116px; width: 88px; height: 88px;
    border-radius: 50%; background: var(--paper);
    display: flex; align-items: center; justify-content: center; text-align: center;
    color: var(--brand-blue); font-size: 10px; font-weight: 700; line-height: 1.25; letter-spacing: 0.5px;
  }

  .property { position: absolute; right: 26px; top: 122px; text-align: right; }
  .property-name { color: var(--brand-blue); font-size: 20px; font-weight: 700; }
  .property-address { color: var(--mid-grey); font-size: 13.5px; margin-top: 2px; }

  .contact { position: absolute; right: 26px; top: 190px; text-align: right; color: var(--ink); font-size: 14.5px; line-height: 19px; list-style: none; }

  /* Back */
  .card-back { left: 720px; top: 210px; width: 320px; height: 560px; }
  .back-watermark {
    position: absolute; left: 70px; top: 190px; width: 330px; height: 330px;
    border-radius: 50%; background: var(--watermark);
  }
  .back-brand { position: absolute; left: 34px; top: 46px; color: var(--brand-blue); font-weight: 900; }
  .back-brand .word { display: block; font-size: 34px; line-height: 1; letter-spacing: 0.5px; }
  .back-brand .sub { display: block; font-size: 13px; letter-spacing: 3px; margin-top: 4px; }
</style>
</head>
<body>

  <section class="card card-front" aria-label="Business card front">
    <div class="front-band"></div>
    <div class="manager">
      <p class="manager-name"><span class="first">MARISOL</span> <span class="last">DELGADO</span></p>
      <p class="manager-title">Resident Manager</p>
    </div>

    <div class="brand-tab"></div>
    <div class="brand-seal">HARBORVIEW<br>ESTATES</div>

    <div class="property">
      <p class="property-name">Cedar Crest Apartments</p>
      <p class="property-address">2485 Larkin Avenue Oceanside, CA 92054</p>
    </div>

    <ul class="contact">
      <li>O: 555-210-4830</li>
      <li>F: 555-210-4831</li>
      <li>C: 555-318-6627</li>
      <li>E: marisol@harborviewest.com</li>
    </ul>
  </section>

  <section class="card card-back" aria-label="Business card back">
    <div class="back-watermark"></div>
    <p class="back-brand">
      <span class="word">HARBORVIEW</span>
      <span class="sub">ESTATES LLC</span>
    </p>
  </section>

</body>
</html>
```